Investment company needing business card

We are wanting a business card which looks sharp and easy on the eye. We are thinking of having a business card with the logo embossed on it, to really make it stand out. We will only have a small amount of information of the business card, person's name, position, email address and phone number

Contact Information for Business Card

Danielle Frost
Executive Assistant
+64 21 473 5162
danielf@harwickpartners.co.nz

Requirements
Must have
• Embossed logo
Should not have
• Not to be busy

```html
<!DOCTYPE html>
<html lang="en">
<head>
<meta charset="utf-8">
<title>Harwick Partners – Business Card</title>
<link href="https://fonts.googleapis.com/css2?family=Lato:wght@400;700;900&display=swap" rel="stylesheet">
<style>
  :root {
    --backdrop: #e9e7e3;
    --card-white: #f6f6f5;
    --band-grey: #7d7d7d;
    --band-green: #2fc596;
    --ink-green: #25b583;
    --ink-grey: #6a6a6a;
    --text-light: #ffffff;
  }
  * { margin: 0; padding: 0; box-sizing: border-box; }
  html, body {
    width: 1200px; height: 780px; overflow: hidden;
    background: var(--backdrop);
    font-family: "Lato", sans-serif;
  }
  .card {
    position: absolute; left: 100px; top: 110px;
    width: 1000px; height: 560px;
    background: var(--card-white);
    border-radius: 22px;
    overflow: hidden;
    box-shadow: 0 18px 40px rgba(0,0,0,0.18);
  }
  .brand {
    position: absolute; left: 190px; top: 92px;
    display: flex; align-items: center; gap: 26px;
  }
  .brand-mark {
    width: 76px; height: 76px;
    background: var(--ink-green);
  }
  .brand-name {
    font-weight: 900; font-size: 64px; line-height: 1;
    letter-spacing: 2px; text-transform: uppercase;
    color: var(--ink-green);
  }
  .band-title {
    position: absolute; left: 0; top: 262px;
    width: 100%; height: 54px;
    background: var(--band-grey);
    display: flex; align-items: center;
    padding-left: 320px;
    color: var(--text-light);
    font-size: 26px;
  }
  .person-name { font-weight: 700; text-transform: uppercase; letter-spacing: 0.5px; }
  .divider { margin: 0 14px; opacity: 0.9; }
  .person-role { font-weight: 400; }
  .band-contact {
    position: absolute; left: 0; top: 316px;
    width: 100%; height: 186px;
    background: var(--band-green);
    padding: 62px 0 0 460px;
    color: var(--text-light);
    font-size: 25px; line-height: 1.35;
  }
  .contact-label { font-weight: 700; margin-right: 6px; }
</style>
</head>
<body>
  <div class="card">
    <div class="brand">
      <div class="brand-mark"></div>
      <div class="brand-name">Harwick Partners</div>
    </div>
    <div class="band-title">
      <span class="person-name">Danielle Frost</span>
      <span class="divider">|</span>
      <span class="person-role">Executive Assistant</span>
    </div>
    <div class="band-contact">
      <p class="contact-line"><span class="contact-label">P:</span>+64 21 473 5162</p>
      <p class="contact-line"><span class="contact-label">E:</span>danielf@harwickpartners.co.nz</p>
    </div>
  </div>
</body>
</html>
```